Corporate Business Card

Very professional, Modern, Not to busy, include phone address email, website
(253) 617-4930, 18761 52nd Avenue S, Kent, WA 98047, martin@plumlinegroup.com, varkoworks.com

Target Market(s)

Manufacturing

Industry/Entity Type

Aero, machining, manufacturing, Off road racing

Contact Information for Business Card

Phone, address email, website

```html
<!DOCTYPE html>
<html lang="en">
<head>
<meta charset="utf-8">
<title>Varko Works – Business Card</title>
<link rel="stylesheet" href="https://fonts.googleapis.com/css2?family=Arimo:wght@400;700&display=swap">
<style>
  :root {
    --page: #e4e4e2;
    --navy: #21366b;
    --red: #c8161d;
    --white: #ffffff;
    --line: rgba(255,255,255,0.85);
  }
  * { box-sizing: border-box; margin: 0; padding: 0; }
  html, body { width: 1200px; height: 801px; overflow: hidden; }
  body {
    background: var(--page);
    font-family: "Arimo", Arial, sans-serif;
    position: relative;
  }
  .card {
    position: absolute;
    top: 246px;
    width: 540px;
    height: 308px;
    background: var(--navy);
    overflow: hidden;
    color: var(--white);
  }
  .card--front { left: 40px; }
  .card--back { left: 620px; }

  .wordmark {
    position: absolute;
    display: flex;
    align-items: center;
    gap: 10px;
    font-weight: 700;
    color: var(--white);
    letter-spacing: 0.04em;
    white-space: nowrap;
  }
  .wordmark__square { background: var(--red); flex: none; }
  .card--front .wordmark { left: 40px; top: 62px; font-size: 40px; }
  .card--front .wordmark__square { width: 16px; height: 16px; }
  .card--back .wordmark { left: 50%; top: 120px; transform: translateX(-50%); font-size: 50px; }
  .card--back .wordmark__square { width: 20px; height: 20px; }

  .rule { position: absolute; height: 1.5px; background: var(--line); }
  .card--front .rule { left: 34px; top: 136px; width: 210px; }
  .card--back .rule { left: 60px; top: 196px; width: 240px; }

  .person { position: absolute; left: 110px; top: 160px; text-align: right; width: 168px; }
  .person__name { color: var(--red); font-size: 18px; font-weight: 400; letter-spacing: 0.03em; }
  .person__role { color: var(--white); font-size: 13px; margin-top: 3px; }

  .divider { position: absolute; left: 292px; top: 150px; width: 1px; height: 70px; background: var(--line); }

  .contacts { position: absolute; left: 306px; top: 150px; list-style: none; }
  .contacts li { display: flex; align-items: center; gap: 8px; font-size: 12px; line-height: 23px; }
  .contacts svg { width: 12px; height: 12px; flex: none; }

  .bands { position: absolute; left: 0; bottom: 0; width: 540px; height: 50px; }
  .address {
    position: absolute; left: 160px; bottom: 22px; width: 250px;
    font-size: 12.5px; line-height: 24px; text-align: center; color: var(--white);
  }
</style>
</head>
<body>
  <section class="card card--front" aria-label="Business card front">
    <div class="wordmark"><span class="wordmark__square"></span>VARKO WORKS</div>
    <div class="rule"></div>

    <div class="person">
      <p class="person__name">DANIEL REYES</p>
      <p class="person__role">Manager</p>
    </div>

    <div class="divider"></div>

    <ul class="contacts">
      <li>
        <svg viewBox="0 0 12 12" aria-hidden="true"><path fill="#c8161d" d="M2.4 0.8l2 2-1.1 1.3c.7 1.5 1.9 2.7 3.4 3.4l1.3-1.1 2 2-1.2 1.9C5.6 10.3 1.7 6.4 0.5 2z"/></svg>
        (253) 617-4930
      </li>
      <li>
        <svg viewBox="0 0 12 12" aria-hidden="true"><rect x="0.5" y="2" width="11" height="8" fill="#c8161d"/><path d="M0.8 2.4L6 6.6l5.2-4.2" fill="none" stroke="#21366b" stroke-width="1"/></svg>
        martin@plumlinegroup.com
      </li>
      <li>
        <svg viewBox="0 0 12 12" aria-hidden="true"><circle cx="6" cy="6" r="5.5" fill="#c8161d"/><path d="M0.5 6h11M6 0.5c-2.5 3-2.5 8 0 11M6 0.5c2.5 3 2.5 8 0 11" fill="none" stroke="#21366b" stroke-width="0.9"/></svg>
        www.varkoworks.com
      </li>
    </ul>

    <svg class="bands" viewBox="0 0 540 50" aria-hidden="true">
      <polygon points="0,16 150,16 118,50 0,50" fill="#ffffff"/>
      <polygon points="162,4 420,4 400,28 142,28" fill="#c8161d"/>
      <polygon points="436,4 540,4 540,30 414,30" fill="#ffffff"/>
    </svg>
    <p class="address">18761 52nd Avenue S, Kent, WA 98047</p>
  </section>

  <section class="card card--back" aria-label="Business card back">
    <div class="wordmark"><span class="wordmark__square"></span>VARKO WORKS</div>
    <div class="rule"></div>
  </section>
</body>
</html>
```